Brevlon Website Design - Wordpress

Need a website WordPress design for our existing website that we just stood up. The logo is already in place and name. Brevlon.example We are a company which makes connections with our clients through educating them and providing networking events. We would like for the website to show a VIP/special feel to it.

Target Market(s)

Business executives and employees. Age group 26-65 in the following sectors:
- Technology
- Human Resources
- Finance
- Sales

Industry/Entity Type

Technical Service

Number of Pages Required

4 page

Font styles to use
Sans Serif

Requirements
Must have
• Must be something for Wordpress
Nice to have
• Would like this to be professional but look cutting edge and VIP.

```html
<!DOCTYPE html>
<html lang="en">
<head>
<meta charset="utf-8">
<title>Brevlon Connected</title>
<link href="https://fonts.googleapis.com/css2?family=Raleway:wght@300;400;500;600;700&display=swap" rel="stylesheet">
<style>
:root{
  --gold:#e3a912;
  --gold-dark:#c9940c;
  --ink:#1d1d1f;
  --dark:#141518;
  --grey-text:#5c5c5c;
  --blue:#1167a8;
  --purple:#7b3c97;
  --yellow:#e2ab11;
  --red:#d22a2a;
  --light-card:#efefef;
  --white:#ffffff;
}
*{margin:0;padding:0;box-sizing:border-box}
html,body{width:1200px;height:3346px;overflow:hidden}
body{font-family:'Raleway',sans-serif;color:var(--ink);background:var(--white);position:relative}
.abs{position:absolute}
.btn{position:absolute;background:var(--gold);color:var(--white);font-size:19px;font-weight:500;display:flex;align-items:center;justify-content:center;letter-spacing:.5px}

/* hero */
.hero{position:absolute;left:0;top:0;width:1200px;height:678px;background:linear-gradient(100deg,#2a2624 0%,#4a4540 30%,#3b3a3a 55%,#2b2d30 80%,#1e1f22 100%)}
.hero-photo{position:absolute;inset:0;background:radial-gradient(circle at 30% 25%,rgba(140,110,90,.45),transparent 35%),radial-gradient(circle at 65% 25%,rgba(170,150,130,.35),transparent 35%)}
.hero-shade{position:absolute;inset:0;background:rgba(0,0,0,.35)}
.logo{position:absolute;display:flex;align-items:center;gap:14px;color:var(--white);font-size:32px;font-weight:500;letter-spacing:5px}
.logo-mark{width:40px;height:40px;background:var(--gold)}
.nav{position:absolute;top:36px;left:722px;display:flex;gap:32px;font-size:15px;color:var(--white);font-weight:500}
.nav .active{color:var(--gold);border-bottom:2px solid var(--gold);padding-bottom:8px}
.hero h1{position:absolute;top:282px;width:1200px;text-align:center;color:var(--white);font-size:52px;font-weight:700}
.hero p{position:absolute;top:356px;left:230px;width:740px;text-align:center;color:#e8e8e8;font-size:15px;line-height:26px}

/* tiles */
.tiles{position:absolute;top:678px;left:0;width:1200px;height:275px;display:flex}
.tile{flex:1;display:flex;flex-direction:column;align-items:center;color:var(--white);padding-top:60px}
.tile svg{width:86px;height:86px}
.tile .name{font-size:23px;margin-top:20px}
.tile .sub{font-size:14px;margin-top:4px;opacity:.85}

/* welcome */
.welcome-pre{top:1046px;left:180px;font-size:20px}
.welcome-title{top:1080px;left:178px;font-size:42px;font-weight:400;letter-spacing:.5px}
.values{top:1152px;left:178px;font-size:17px;color:var(--gold)}
.welcome-text{top:1190px;left:178px;width:490px;font-size:14px;line-height:27px;color:var(--grey-text)}
.welcome-photo{left:727px;top:1053px;width:395px;height:292px;background:linear-gradient(135deg,#3b3a52,#8c8aa0 50%,#d7d6df)}

/* offer */
.offer{position:absolute;top:1463px;left:0;width:1200px;height:695px;background:linear-gradient(180deg,#25272c,#141518 60%,#0f1012)}
.offer h2{position:absolute;top:58px;width:1200px;text-align:center;color:var(--white);font-size:46px;font-weight:300}
.offer-box{left:198px;top:177px;width:810px;height:240px;background:rgba(196,150,18,.85)}
.offer-person{left:290px;top:142px;width:190px;height:300px;background:linear-gradient(180deg,#c9a58a,#5b5b5b 40%,#2e2e2e);border-radius:6px}
.offer-title{left:545px;top:218px;color:var(--white);font-size:36px;font-weight:400}
.offer-text{left:545px;top:272px;width:430px;color:#fff6df;font-size:14px;line-height:27px}
.offer-btn{left:545px;top:340px;width:165px;height:46px;border-radius:23px;background:var(--gold);color:var(--white);font-size:17px;display:flex;align-items:center;justify-content:center}
.timeline{left:60px;top:512px;width:1080px;height:1px;background:rgba(255,255,255,.15)}
.step{position:absolute;top:480px;width:240px;text-align:center;color:var(--white)}
.step .dot{margin:0 auto;width:10px;height:10px;border-radius:50%;margin-top:27px}
.step .big{width:70px;height:70px;border-radius:50%;background:var(--gold);margin:-2px auto 0;display:flex;align-items:center;justify-content:center}
.step .label{font-size:15px;margin-top:28px;letter-spacing:.5px}
.step .big+.label{margin-top:16px}
.step .desc{font-size:13px;color:#9c9c9c;line-height:23px;margin-top:6px}

/* cta */
.cta{position:absolute;top:2158px;left:0;width:1200px;height:207px;background:linear-gradient(90deg,#10549c 0%,#2f4f9a 50%,#6b3f93 100%)}
.cta p{position:absolute;left:78px;top:62px;width:680px;color:var(--white);font-size:28px;line-height:42px}

/* meetup */
.meetup-title{top:2414px;width:1200px;text-align:center;font-size:46px;font-weight:400}
.event-card{left:165px;top:2510px;width:870px;height:300px;background:var(--light-card);border-radius:16px;overflow:hidden}
.event-photo{position:absolute;left:0;top:0;width:340px;height:300px;background:linear-gradient(135deg,#9fb6c8,#3d5a78 55%,#1c2b3e)}
.event-title{left:397px;top:42px;width:440px;font-size:25px;line-height:36px}
.event-meta{left:397px;display:flex;align-items:center;gap:14px;color:var(--blue);font-size:16px;font-weight:600}
.event-meta svg{width:20px;height:20px}

/* search */
.search-band{position:absolute;top:2875px;left:0;width:1200px;height:137px;background:var(--gold)}
.search-input{left:288px;top:47px;width:624px;height:50px;background:var(--white);display:flex;align-items:center;padding:0 18px;gap:12px;color:#999;font-size:14px}

/* footer */
.footer{position:absolute;top:3012px;left:0;width:1200px;height:334px;background:var(--dark);color:var(--white)}
.footer h4{position:absolute;top:36px;font-size:17px;font-weight:500;letter-spacing:1px}
.footer .about{left:78px;top:118px;width:240px;font-size:13px;line-height:26px;color:#cfcfcf}
.sitemap{left:345px;top:80px;list-style:none;font-size:13px;color:#cfcfcf}
.sitemap li{height:33px;display:flex;align-items:center;gap:14px}
.sitemap li::before{content:"";width:6px;height:6px;border-radius:50%;background:var(--gold)}
.contact-row{left:608px;display:flex;align-items:center;gap:14px;font-size:13px;color:#cfcfcf}
.social{left:873px;display:flex;align-items:center;gap:16px;font-size:13px;color:#cfcfcf}
.social span.c{width:40px;height:40px;border-radius:50%}
.copyright{top:3300px;width:1200px;text-align:center;font-size:13px;color:#cfcfcf}
</style>
</head>
<body>

<header class="hero">
  <div class="hero-photo" role="img" aria-label="Two colleagues working together at a desk with computers"></div>
  <div class="hero-shade"></div>
  <div class="logo" style="left:78px;top:22px"><span class="logo-mark"></span>BREVLON</div>
  <nav class="nav">
    <span class="active">Events</span><span>Expand</span><span>X</span><span>About</span><span>Connect</span>
    <svg width="16" height="16" viewBox="0 0 16 16"><circle cx="6.5" cy="6.5" r="5" fill="none" stroke="#fff" stroke-width="2"/><line x1="10" y1="10" x2="15" y2="15" stroke="#fff" stroke-width="2.4"/></svg>
  </nav>
  <h1>Expand Your Business</h1>
  <p>Our team is an unusual mix. We're globally experienced, technically capable, community focussed and highly fruitful. The four core values above inform everything we do.</p>
  <div class="btn" style="left:513px;top:428px;width:172px;height:50px">CONTACT US</div>
</header>

<section class="tiles">
  <div class="tile" style="background:var(--blue)">
    <svg viewBox="0 0 86 86"><circle cx="43" cy="40" r="34" fill="#fff"/><text x="43" y="55" text-anchor="middle" font-family="Raleway,sans-serif" font-size="40" font-weight="700" fill="#1167a8">?</text></svg>
    <div class="name">Mind</div><div class="sub">Thought</div>
  </div>
  <div class="tile" style="background:var(--purple)">
    <svg viewBox="0 0 86 86"><circle cx="43" cy="43" r="34" fill="none" stroke="#fff" stroke-width="3" stroke-dasharray="4 5"/><circle cx="43" cy="34" r="9" fill="#fff"/><path d="M25 66 Q43 42 61 66Z" fill="#fff"/></svg>
    <div class="name">Soul</div><div class="sub">Intuition</div>
  </div>
  <div class="tile" style="background:var(--yellow)">
    <svg viewBox="0 0 86 86"><path d="M43 76 L10 42 A18 18 0 0 1 43 18 A18 18 0 0 1 76 42Z" fill="#fff"/><polyline points="12,44 32,44 38,32 46,56 52,44 74,44" fill="none" stroke="#e2ab11" stroke-width="4"/></svg>
    <div class="name">Heart</div><div class="sub">Emotions</div>
  </div>
  <div class="tile" style="background:var(--red)">
    <svg viewBox="0 0 86 86"><rect x="16" y="14" width="54" height="58" rx="8" fill="#fff"/><line x1="30" y1="14" x2="30" y2="38" stroke="#d22a2a" stroke-width="3"/><line x1="43" y1="14" x2="43" y2="38" stroke="#d22a2a" stroke-width="3"/><line x1="56" y1="14" x2="56" y2="38" stroke="#d22a2a" stroke-width="3"/></svg>
    <div class="name">Strength</div><div class="sub">Energy</div>
  </div>
</section>

<section class="welcome">
  <div class="abs welcome-pre">Welcome To</div>
  <h2 class="abs welcome-title">BREVLON CONNECTED</h2>
  <div class="abs values">Virtue | Appreciation | Respect | Ownership</div>
  <p class="abs welcome-text">Our team is an unusual mix. We're globally experienced, technically capable, community focussed and highly fruitful. The four core values above inform everything we do. Our special sauce is knowing how to fuse structure and productivity with relationship and creativity.</p>
  <div class="btn" style="left:178px;top:1318px;width:172px;height:52px">LEARN MORE</div>
  <div class="abs welcome-photo" role="img" aria-label="Two colleagues reviewing work on a computer in an office"></div>
</section>

<section class="offer">
  <h2>What We Offer You</h2>
  <div class="abs offer-box"></div>
  <div class="abs offer-person" role="img" aria-label="Person sitting with a laptop"></div>
  <div class="abs offer-title">EDUCATE</div>
  <p class="abs offer-text">At BREVLON, we provide effective training and learning as the foundation for building a healthy, successful company.</p>
  <div class="abs offer-btn">X - VALUE</div>
  <div class="abs timeline"></div>
  <div class="step" style="left:83px">
    <div class="big"><svg width="36" height="30" viewBox="0 0 36 30"><path d="M18 2 L35 10 L18 18 L1 10Z" fill="none" stroke="#fff" stroke-width="2"/><path d="M8 14 V22 Q18 28 28 22 V14" fill="none" stroke="#fff" stroke-width="2"/></svg></div>
    <div class="label">EDUCATE</div><div class="desc">At BREVLON, we provide<br>effective training &amp; learning.</div>
  </div>
  <div class="step" style="left:348px"><div class="dot" style="background:#c25adf;box-shadow:0 0 10px #c25adf"></div><div class="label">EQUIP</div><div class="desc">Through our connected<br>ecosystem of companies...</div></div>
  <div class="step" style="left:613px"><div class="dot" style="background:#3fb6f0;box-shadow:0 0 10px #3fb6f0"></div><div class="label">EXPAND</div><div class="desc">Our goal is to help you and<br>your business increase...</div></div>
  <div class="step" style="left:878px"><div class="dot" style="background:#f04747;box-shadow:0 0 10px #f04747"></div><div class="label">EXCHANGE</div><div class="desc">We connect you with others<br>who have successfully...</div></div>
</section>

<section class="cta">
  <p>If You need an have any question for connect with us today !</p>
  <div class="btn" style="left:865px;top:105px;width:257px;height:50px">CONNECT WITH US</div>
</section>

<section class="meetup">
  <h2 class="abs meetup-title">Meetup</h2>
  <div class="abs event-card">
    <div class="event-photo" role="img" aria-label="Two businessmen looking at a tablet"></div>
    <div class="abs event-title">BREVLON : Education and Networking Events</div>
    <div class="abs event-meta" style="top:130px"><svg viewBox="0 0 20 20"><rect x="2" y="4" width="16" height="14" fill="none" stroke="#e3a912" stroke-width="2"/><line x1="2" y1="8" x2="18" y2="8" stroke="#e3a912" stroke-width="2"/></svg>March 21, 2019</div>
    <div class="abs event-meta" style="top:166px"><svg viewBox="0 0 20 20"><circle cx="10" cy="6" r="4" fill="#e3a912"/><path d="M3 19 Q10 8 17 19Z" fill="#e3a912"/></svg>Lakeside, Northland</div>
    <div class="btn" style="left:397px;top:212px;width:155px;height:51px">CONNECT</div>
  </div>
</section>

<section class="search-band">
  <svg class="abs" style="left:196px;top:14px" width="104" height="104" viewBox="0 0 104 104"><circle cx="42" cy="42" r="30" fill="none" stroke="#fff" stroke-width="7"/><line x1="64" y1="64" x2="96" y2="96" stroke="#fff" stroke-width="12" stroke-linecap="round"/></svg>
  <div class="abs search-input">
    <svg width="14" height="14" viewBox="0 0 16 16"><circle cx="6.5" cy="6.5" r="5" fill="none" stroke="#333" stroke-width="2"/><line x1="10" y1="10" x2="15" y2="15" stroke="#333" stroke-width="2.4"/></svg>
    <span style="flex:1">Search Here...</span>
    <svg width="16" height="10" viewBox="0 0 16 10"><path d="M0 0 H16 L8 10Z" fill="#333"/></svg>
  </div>
</section>

<footer class="footer">
  <div class="logo" style="left:78px;top:40px;font-size:28px"><span class="logo-mark" style="width:34px;height:34px"></span>BREVLON</div>
  <p class="abs about">Our team is an unusual mix. We're globally experienced, technically capable, community focussed and highly fruitful.</p>
  <h4 style="left:345px">SITEMAP</h4>
  <ul class="abs sitemap"><li>Events</li><li>Expand</li><li>X</li><li>About</li><li>Connect</li></ul>
  <h4 style="left:608px">CONTACT US</h4>
  <div class="abs contact-row" style="top:86px"><svg width="18" height="18" viewBox="0 0 18 18"><path d="M3 1 L7 1 L8 5 L6 7 Q8 11 11 12 L13 10 L17 11 L17 15 Q10 17 5 12 Q1 7 3 1Z" fill="#e3a912"/></svg>1-800-555-0142</div>
  <div class="abs contact-row" style="top:122px"><svg width="18" height="14" viewBox="0 0 18 14"><rect width="18" height="14" fill="#e3a912"/><polyline points="0,0 9,8 18,0" fill="none" stroke="#141518" stroke-width="1.5"/></svg>connect@brevlon.example</div>
  <h4 style="left:873px">FOLLOW US</h4>
  <div class="abs social" style="top:82px"><span class="c" style="background:#3b5998"></span>Circlebook</div>
  <div class="abs social" style="top:133px"><span class="c" style="background:#1da1f2"></span>Chirper</div>
  <div class="abs social" style="top:184px"><span class="c" style="background:#0e76a8"></span>Linkwork</div>
</footer>
<div class="abs copyright">©BREVLON CONNECTED - 2019 All Right Reserved.</div>

</body>
</html>
```